Business Card for Financial Asset Management Company

Now we are launching a new company based in Tokyo.
The company information is below;

Company Name: Velmora Advisory

Operations: Financial assets management, Proposing forming portfolio of assets, Consulting service, and advising to enhance your company's financial health

Corporate Colour: Japan Blue or Navy like below
http://stuweb.ax.tolvaric.edu/kpimra/pics/Shade/Mist-Shade-217.jpg

It's dark and deep, and will get to fit to our clients as our relationships last longer and longer.

Our images for this colour are "Japanese style" and "pride in our craftmanship" , and also "gentle".

Corporate Key Image: an order taker who is sincere, polite, but courageous

We don't have our logo yet so please feel free to put any symbol on your design.

Please do not hesitate about asking any questions.
Thank you :-)

Reason: We are still discussin on final decision. Thank you for your understanding.

```html
<!DOCTYPE html>
<html lang="en">
<head>
<meta charset="utf-8">
<title>Velmora Advisory – Business Card</title>
<link rel="stylesheet" href="https://fonts.googleapis.com/css2?family=Open+Sans:wght@400;700&display=swap">
<style>
  :root {
    --navy: #0d4fa3;
    --sky: #1b7fc4;
    --ink: #1a1a1a;
    --rule: #c9cacc;
    --wave: #d0d1d3;
    --wave-light: #e4e5e7;
    --band: #1075c1;
    --paper: #ffffff;
  }
  * { margin: 0; padding: 0; box-sizing: border-box; }
  html, body {
    width: 1200px;
    height: 726px;
    overflow: hidden;
    background: var(--paper);
  }
  .card {
    position: relative;
    width: 1200px;
    height: 726px;
    background: var(--paper);
    font-family: "Open Sans", Arial, sans-serif;
    line-height: 1;
  }
  .brand-mark {
    position: absolute;
    left: 84px;
    top: 76px;
    width: 134px;
    height: 134px;
    border-radius: 50%;
    background: var(--navy);
  }
  .brand-name {
    position: absolute;
    left: 240px;
    font-size: 46px;
    font-weight: 400;
    color: var(--navy);
    white-space: nowrap;
  }
  .brand-name--first { top: 106px; }
  .brand-name--second { top: 155px; }
  .divider {
    position: absolute;
    left: 199px;
    top: 273px;
    width: 2px;
    height: 274px;
    background: var(--rule);
  }
  .person-name {
    position: absolute;
    left: 242px;
    top: 270px;
    font-size: 38px;
    font-weight: 700;
    color: var(--navy);
  }
  .person-title {
    position: absolute;
    left: 242px;
    top: 322px;
    font-size: 29px;
    font-weight: 400;
    color: var(--sky);
  }
  .contact-line {
    position: absolute;
    left: 242px;
    font-size: 31px;
    font-weight: 400;
    color: var(--ink);
    white-space: nowrap;
  }
  .contact-line--email { top: 378px; }
  .contact-line--phone { top: 424px; }
  .contact-line--building { top: 471px; }
  .contact-line--street { top: 518px; }
  .separator { padding: 0 14px; }
  .wave-pattern {
    position: absolute;
    left: 0;
    top: 592px;
    width: 1200px;
    height: 122px;
    background: linear-gradient(180deg, var(--wave-light) 0%, var(--wave) 100%);
  }
  .base-band {
    position: absolute;
    left: 0;
    bottom: 0;
    width: 1200px;
    height: 12px;
    background: var(--band);
  }
</style>
</head>
<body>
  <div class="card">
    <div class="brand-mark" aria-hidden="true"></div>
    <div class="brand-name brand-name--first">Velmora</div>
    <div class="brand-name brand-name--second">Advisory</div>

    <div class="divider" aria-hidden="true"></div>

    <div class="person-name">Haruna Sato</div>
    <div class="person-title">General Director</div>

    <div class="contact-line contact-line--email">haruna.sato@velmoraadvisory.jp</div>
    <div class="contact-line contact-line--phone">Tel. 090 555 0142<span class="separator">|</span>Fax. 090 555 0176</div>
    <div class="contact-line contact-line--building">Minato Grand Pine Tower</div>
    <div class="contact-line contact-line--street">2-8, Kyobashi 3-Chome, Chuo-ku, Tokyo 104-0031</div>

    <div class="wave-pattern" role="img" aria-label="Traditional Japanese seigaiha wave pattern in light grey across the bottom of the card"></div>
    <div class="base-band" aria-hidden="true"></div>
  </div>
</body>
</html>
```